Business card design Needed for new logo / Construction business, home extensions and new builds

We need a business card design using our new logo files which i will attach to this project :)

We are a small construction business specialising in home extensions, new builds and property development. We are very ambitious and would appreciate professional and elegant designs for our new business card.

Very serious about using the services on MakerQuarry and recently acquired our new logo from here :)

Please get involved, i will feedback when i can as i am very busy but can respond daily, thanks

Target Market(s)

People that want to build onto their houses, new building developments or adding too their existing property

Industry/Entity Type

Construction

Contact Information for Business Card

Renwick Tolliver Construction, Lionel Ashby (Managing Director), Tel 07822254961, email - info@renwick-tolliver, www.renwick-tolliver.co.uk

Colors

Designer to choose colors to be used in the design.

Requirements
Must have
• I like a deep grey on the back please. A lot of you have provided black from and back, try mixing things up a little. The black looks cool 😎 Thanks

```html
<!DOCTYPE html>
<html lang="en">
<head>
<meta charset="utf-8">
<title>Renwick Tolliver Construction – Business Card</title>
<link rel="stylesheet" href="https://fonts.googleapis.com/css2?family=Open+Sans:wght@400;600;700&display=swap">
<style>
  :root {
    --stage: #2b2d31;
    --card: #1f1f23;
    --card-back: #26272b;
    --gold: #d9a637;
    --gold-light: #f6d98a;
    --gold-deep: #b98320;
    --silver: #d6d8dc;
    --white: #f4f4f4;
  }
  * { box-sizing: border-box; margin: 0; padding: 0; }
  html, body {
    width: 1200px; height: 780px; overflow: hidden;
    background: var(--stage);
    font-family: "Open Sans", Arial, sans-serif;
  }
  .card {
    position: absolute;
    width: 540px; height: 310px;
    border-radius: 22px;
    overflow: hidden;
    box-shadow: 0 14px 30px rgba(0,0,0,.45);
  }
  .card--front { left: 40px; top: 235px; background: var(--card); }
  .card--back  { left: 620px; top: 235px; background: var(--card-back); }

  .front-band { position: absolute; inset: 0; width: 540px; height: 310px; }
  .address-text {
    font-family: "Open Sans", Arial, sans-serif;
    font-size: 14px;
    fill: var(--white);
  }

  .wordmark {
    color: var(--gold);
    font-weight: 600;
    text-transform: uppercase;
    text-align: center;
    line-height: 1.25;
  }
  .wordmark--small { position: absolute; right: 40px; top: 44px; font-size: 12px; letter-spacing: 1.5px; }
  .wordmark--large { font-size: 24px; letter-spacing: 3px; }

  .person { position: absolute; left: 70px; top: 62px; }
  .person__name { font-size: 27px; font-weight: 700; color: var(--silver); letter-spacing: .3px; }
  .person__name span { color: var(--gold); }
  .person__role { font-size: 13px; color: var(--white); margin-top: 2px; padding-left: 40px; }

  .divider { position: absolute; left: 258px; top: 128px; width: 2px; height: 62px; background: var(--white); }

  .contacts { position: absolute; left: 278px; top: 128px; list-style: none; }
  .contacts li { display: flex; align-items: center; gap: 8px; font-size: 14px; color: var(--white); height: 21px; }
  .contacts svg { width: 12px; height: 12px; fill: var(--gold); flex: none; }

  .back-lockup {
    position: absolute; inset: 0;
    display: flex; align-items: center; justify-content: center;
  }
  .back-lockup__mark { display: flex; align-items: center; gap: 12px; }
  .back-lockup__square { width: 14px; height: 14px; background: var(--gold); }
</style>
</head>
<body>

<section class="card card--front" aria-label="Business card front">
  <svg class="front-band" viewBox="0 0 540 310">
    <defs>
      <linearGradient id="goldSweep" x1="0" y1="0" x2="1" y2="0.3">
        <stop offset="0" stop-color="#c28a24"/>
        <stop offset=".25" stop-color="#f6d98a"/>
        <stop offset=".55" stop-color="#d9a637"/>
        <stop offset=".8" stop-color="#f3cf76"/>
        <stop offset="1" stop-color="#c28a24"/>
      </linearGradient>
      <linearGradient id="silverSweep" x1="0" y1="0" x2="1" y2="0">
        <stop offset="0" stop-color="#6d6f74"/>
        <stop offset=".5" stop-color="#eeeeef"/>
        <stop offset="1" stop-color="#8c8e93"/>
      </linearGradient>
      <path id="addressLine" d="M22 190 C100 202 180 246 300 280 C340 291 380 296 420 298"/>
    </defs>
    <path d="M0 150 C90 160 180 215 300 250 C380 272 450 278 540 262 L540 310 L0 310 Z" fill="url(#goldSweep)"/>
    <path d="M40 138 C120 152 200 204 310 238 C390 262 450 270 500 266" fill="none" stroke="url(#silverSweep)" stroke-width="3"/>
    <text class="address-text"><textPath href="#addressLine">Quarry Lane, Elmsworth Dunmoor, DM4 2RT</textPath></text>
  </svg>

  <div class="wordmark wordmark--small">Renwick Tolliver<br>Construction</div>

  <div class="person">
    <p class="person__name">Lionel <span>Ashby</span></p>
    <p class="person__role">Managing Director</p>
  </div>

  <div class="divider"></div>

  <ul class="contacts">
    <li>
      <svg viewBox="0 0 24 24" aria-hidden="true"><path d="M6.6 10.8a15.1 15.1 0 0 0 6.6 6.6l2.2-2.2c.3-.3.7-.4 1-.2 1.1.4 2.3.6 3.6.6.6 0 1 .4 1 1V20c0 .6-.4 1-1 1A17 17 0 0 1 3 4c0-.6.4-1 1-1h3.5c.6 0 1 .4 1 1 0 1.3.2 2.5.6 3.6.1.3 0 .7-.2 1z"/></svg>
      0782 225 4961
    </li>
    <li>
      <svg viewBox="0 0 24 24" aria-hidden="true"><path d="M2 5h20v14H2z M3.5 6.5 12 13l8.5-6.5"/></svg>
      info@renwick-tolliver.co.uk
    </li>
    <li>
      <svg viewBox="0 0 24 24" aria-hidden="true"><circle cx="12" cy="12" r="10"/></svg>
      www.renwick-tolliver.co.uk
    </li>
  </ul>
</section>

<section class="card card--back" aria-label="Business card back">
  <div class="back-lockup">
    <div class="back-lockup__mark">
      <span class="back-lockup__square"></span>
      <div class="wordmark wordmark--large">Renwick Tolliver<br>Construction</div>
    </div>
  </div>
</section>

</body>
</html>
```